Moravel Aesthetic Doctor

I require an elegant, luxurious looking business card for my aesthetic business. I am a doctor and that will set me aside from competitors. I am planning to provide home and spa based treatments to clients with high expectations. I have attached my logo.

```html
<!DOCTYPE html>
<html lang="en">
<head>
<meta charset="utf-8">
<title>Moravel Aesthetic Doctor – Business Card</title>
<link href="https://fonts.googleapis.com/css2?family=Arimo:wght@400;700&family=Cormorant+Garamond:wght@400;500&display=swap" rel="stylesheet">
<style>
  :root {
    --stage: #2e2e30;
    --card: #ffffff;
    --ink-grey: #6d6e71;
    --sky: #3fa9e0;
    --sky-deep: #1f73c4;
    --mist: #eef0f2;
    --warm: #e8a24a;
    --stone: #cfcac4;
  }
  * { box-sizing: border-box; margin: 0; padding: 0; }
  html, body { width: 1200px; height: 866px; overflow: hidden; background: var(--stage); }
  .stage { position: relative; width: 1200px; height: 866px; }
  .card {
    position: absolute; left: 250px; width: 700px; height: 390px;
    background: var(--card); overflow: hidden;
    box-shadow: 0 10px 28px rgba(0,0,0,.45);
  }
  .card--front { top: 30px; }
  .card--back { top: 446px; }
  .front__veil {
    position: absolute; inset: 0;
    background:
      radial-gradient(ellipse 260px 190px at 330px 160px, var(--mist), transparent 70%),
      radial-gradient(ellipse 200px 160px at 150px 290px, #f4f5f6, transparent 70%);
  }
  .contact {
    position: absolute; left: 44px; top: 58px;
    font-family: "Arimo", sans-serif; color: var(--ink-grey);
  }
  .contact__name { font-size: 28px; font-weight: 700; letter-spacing: .5px; }
  .contact__post { font-size: 13px; color: var(--sky); font-weight: 400; margin-left: 4px; }
  .contact__diploma { font-size: 16px; color: var(--sky); margin-top: 4px; }
  .contact__list { list-style: none; margin-top: 14px; font-size: 15px; line-height: 24px; }
  .contact__list li { display: flex; align-items: center; gap: 9px; }
  .contact__list svg { width: 14px; height: 14px; fill: none; stroke: var(--sky-deep); stroke-width: 1.6; }
  .brand {
    position: absolute; left: 300px; top: 200px;
    display: flex; align-items: center; gap: 16px;
  }
  .brand__dot { width: 64px; height: 64px; border-radius: 50%; background: var(--sky); }
  .brand__name {
    font-family: "Cormorant Garamond", serif; font-weight: 500;
    font-size: 56px; color: var(--ink-grey); letter-spacing: 6px; line-height: 1;
  }
  .brand__tag {
    font-family: "Cormorant Garamond", serif; font-weight: 500;
    font-size: 24px; color: var(--sky); letter-spacing: 4px; margin-top: 2px;
  }
  .social {
    position: absolute; right: 36px; bottom: 28px;
    display: flex; align-items: center; gap: 8px;
    font-family: "Arimo", sans-serif; font-size: 14px; color: var(--sky-deep);
  }
  .social__dot { width: 14px; height: 14px; border-radius: 50%; background: var(--sky-deep); }
  .collage { display: block; width: 100%; height: 100%; }
</style>
</head>
<body>
<main class="stage">
  <section class="card card--front" aria-label="Business card front">
    <div class="front__veil"></div>
    <div class="contact">
      <h1 class="contact__name">Dr Elise Varrow<span class="contact__post">MRCPCH MD</span></h1>
      <p class="contact__diploma">Australasian Diploma of Aesthetic Medicine</p>
      <ul class="contact__list">
        <li><svg viewBox="0 0 16 16"><path d="M4 2l3 3-2 2c1 2 2 3 4 4l2-2 3 3-2 2C7 14 2 9 2 4z"/></svg>0800 555 019</li>
        <li><svg viewBox="0 0 16 16"><rect x="1.5" y="3.5" width="13" height="9"/><path d="M1.5 3.5l6.5 5 6.5-5"/></svg>elise@moravel.co.nz</li>
        <li><svg viewBox="0 0 16 16"><circle cx="8" cy="8" r="6.5"/><path d="M1.5 8h13M8 1.5c-3 3.5-3 9.5 0 13M8 1.5c3 3.5 3 9.5 0 13"/></svg>www.moravel.co.nz</li>
      </ul>
    </div>
    <div class="brand">
      <span class="brand__dot"></span>
      <div>
        <div class="brand__name">MORAVEL</div>
        <div class="brand__tag">AESTHETIC DOCTOR</div>
      </div>
    </div>
    <div class="social"><span class="social__dot"></span>@moravel</div>
  </section>

  <section class="card card--back" aria-label="Business card back">
    <svg class="collage" viewBox="0 0 700 390" preserveAspectRatio="none">
      <defs>
        <linearGradient id="candles" x1="0" y1="0" x2="1" y2="1"><stop offset="0" stop-color="#3a2a1e"/><stop offset="1" stop-color="#e8a24a"/></linearGradient>
        <linearGradient id="facial" x1="0" y1="0" x2="1" y2="1"><stop offset="0" stop-color="#e9c7bd"/><stop offset="1" stop-color="#d9a6b0"/></linearGradient>
        <linearGradient id="towel" x1="0" y1="0" x2="1" y2="1"><stop offset="0" stop-color="#d8d8da"/><stop offset="1" stop-color="#9c7a55"/></linearGradient>
        <linearGradient id="oils" x1="0" y1="0" x2="1" y2="1"><stop offset="0" stop-color="#eae6e1"/><stop offset="1" stop-color="#c06a48"/></linearGradient>
        <linearGradient id="clay" x1="0" y1="0" x2="1" y2="1"><stop offset="0" stop-color="#e6e3de"/><stop offset="1" stop-color="#4a4a46"/></linearGradient>
      </defs>
      <polygon role="img" aria-label="Photo: candlelit spa setting" fill="url(#candles)" points="0,0 330,0 0,300"/>
      <polygon role="img" aria-label="Photo: gloved hands giving a facial treatment" fill="url(#facial)" points="330,0 700,0 700,70 470,200 280,45"/>
      <polygon role="img" aria-label="Photo: rolled towel, bath bomb and wooden bowl" fill="url(#towel)" points="0,300 280,45 470,200 200,390 0,390"/>
      <polygon role="img" aria-label="Photo: amber skincare bottles and flowers" fill="url(#oils)" points="470,200 700,70 700,250 560,330"/>
      <polygon role="img" aria-label="Photo: clay mask bowl, brush and serum dropper" fill="url(#clay)" points="200,390 470,200 560,330 700,250 700,390"/>
      <g stroke="#ffffff" stroke-width="5" fill="none">
        <line x1="330" y1="0" x2="0" y2="300"/>
        <line x1="280" y1="45" x2="470" y2="200"/>
        <line x1="700" y1="70" x2="470" y2="200"/>
        <line x1="470" y1="200" x2="200" y2="390"/>
        <line x1="470" y1="200" x2="560" y2="330"/>
        <line x1="560" y1="330" x2="700" y2="250"/>
      </g>
    </svg>
  </section>
</main>
</body>
</html>
```